Bramwell IT Services Business Card

Bramwell IT Services are a Perth based IT Services company. We would like to incorporate our company logo (attached) and stick with the blue that is in that design. I would like a clean look design that isn't too busy, yet creates a lasting image that is instantly recognisable in the recipients mind.

Target Market(s)

The target audience is small/medium business owners.

Industry/Entity Type

Business

Font styles to use
Serif
Sans Serif

Colors

Designer to choose colors to be used in the design.

Requirements
Must have
• The design should include:
Business name: Bramwell IT Services
Directors Name: Marcus Tenley
Phone Number: 0483 562 904
Email: support@bramwellit.com.au
Website: www.bramwellit.com.au

```html
<!DOCTYPE html>
<html lang="en">
<head>
<meta charset="utf-8">
<title>Bramwell IT Services – Business Card</title>
<link href="https://fonts.googleapis.com/css2?family=Arimo:wght@400;700&display=swap" rel="stylesheet">
<style>
  :root {
    --backdrop: #e4e5e7;
    --card-front: #f4f5f7;
    --card-back: #3d3e40;
    --brand-blue: #1f63b6;
    --ink-grey: #6b6d70;
    --back-type: #6a6b6e;
    --icon-blue: #2a5fa8;
  }
  * { margin: 0; padding: 0; box-sizing: border-box; }
  html, body { width: 1200px; height: 871px; overflow: hidden; }
  body {
    background: var(--backdrop);
    font-family: "Arimo", Arial, sans-serif;
    position: relative;
  }
  .card {
    position: absolute;
    top: 124px;
    width: 380px;
    height: 622px;
    box-shadow: 0 6px 18px rgba(0,0,0,0.12);
  }
  .card--front { left: 190px; background: var(--card-front); }
  .card--back { left: 630px; background: var(--card-back); }

  .brand {
    position: absolute;
    left: 56px;
    top: 118px;
    display: flex;
    align-items: center;
    gap: 12px;
  }
  .brand__mark { width: 22px; height: 22px; background: var(--brand-blue); }
  .brand__name {
    font-weight: 700;
    font-size: 24px;
    color: var(--brand-blue);
    letter-spacing: 0.5px;
  }
  .person { position: absolute; left: 56px; top: 396px; }
  .person__name { font-size: 21px; color: var(--brand-blue); }
  .person__role { font-size: 15px; color: var(--ink-grey); margin-top: 4px; }

  .contacts {
    position: absolute;
    left: 56px;
    top: 492px;
    list-style: none;
  }
  .contacts__item {
    display: flex;
    align-items: center;
    gap: 10px;
    font-size: 17px;
    color: var(--ink-grey);
    height: 26px;
  }
  .contacts__icon { width: 16px; height: 16px; flex: none; }

  .card--back .brand { left: 56px; top: 270px; }
  .card--back .brand__mark { background: var(--back-type); }
  .card--back .brand__name { color: var(--back-type); }
  .back__web {
    position: absolute;
    right: 40px;
    bottom: 40px;
    font-size: 17px;
    color: var(--back-type);
  }
</style>
</head>
<body>
  <section class="card card--front" aria-label="Business card front">
    <div class="brand">
      <span class="brand__mark"></span>
      <span class="brand__name">Bramwell IT Services</span>
    </div>
    <div class="person">
      <p class="person__name">Marcus Tenley</p>
      <p class="person__role">Director</p>
    </div>
    <ul class="contacts">
      <li class="contacts__item">
        <svg class="contacts__icon" viewBox="0 0 16 16" aria-hidden="true">
          <path d="M2 5c0-2 2-3 6-3s6 1 6 3v1h-3V5H5v1H2z" fill="var(--icon-blue)"/>
          <rect x="3" y="7" width="10" height="7" rx="1" fill="var(--icon-blue)"/>
          <circle cx="8" cy="10.5" r="1.8" fill="var(--card-front)"/>
        </svg>
        0483 562 904
      </li>
      <li class="contacts__item">
        <svg class="contacts__icon" viewBox="0 0 16 16" aria-hidden="true">
          <rect x="1" y="3" width="14" height="10" fill="var(--icon-blue)"/>
          <path d="M1.5 3.5 8 9l6.5-5.5" fill="none" stroke="var(--card-front)" stroke-width="1.2"/>
        </svg>
        support@bramwellit.com.au
      </li>
      <li class="contacts__item">
        <svg class="contacts__icon" viewBox="0 0 16 16" aria-hidden="true">
          <circle cx="8" cy="8" r="7" fill="var(--icon-blue)"/>
          <g fill="none" stroke="var(--card-front)" stroke-width="0.9">
            <ellipse cx="8" cy="8" rx="3" ry="7"/>
            <path d="M1 8h14M2.5 4.5h11M2.5 11.5h11M8 1v14"/>
          </g>
        </svg>
        www.bramwellit.com.au
      </li>
    </ul>
  </section>

  <section class="card card--back" aria-label="Business card back">
    <div class="brand">
      <span class="brand__mark"></span>
      <span class="brand__name">Bramwell IT Services</span>
    </div>
    <p class="back__web">www.bramwellit.com.au</p>
  </section>
</body>
</html>
```